Bramblewood Card Company Business Cards

We are a trading card store with Glimmorax, sports and other TCG cards, we need a business card design that encompasses a clean cut, modern style with a retro flare. website is bramblewoodcardco.com for reference. Can utilize a comic book era feel or a more modern outdoor feel to utilize the "Pacific Northwest" elements of tress, mountains, etc.

Industry/Entity Type

Trading cards and collectibles

Contact Information for Business Card

business name, email address, phone number, name, owner job title

Font styles to use
Sans Serif

```html
<!DOCTYPE html>
<html lang="en">
<head>
<meta charset="utf-8">
<title>Bramblewood Card Company – Business Cards</title>
<link rel="stylesheet" href="https://fonts.googleapis.com/css2?family=Montserrat:wght@400;500;700;800&display=swap">
<style>
  :root {
    --backdrop: #2a2a2c;
    --card: #1e1e20;
    --text-light: #f2f2f2;
    --text-muted: #8a8a8c;
    --accent: #27bfe0;
    --rule: #5a5a5c;
  }
  * { box-sizing: border-box; margin: 0; padding: 0; }
  html, body {
    width: 1200px; height: 900px; overflow: hidden;
    background: var(--backdrop);
    font-family: "Montserrat", Arial, sans-serif;
    color: var(--text-light);
  }
  .sheet {
    width: 1200px; height: 900px;
    display: flex; flex-direction: column; align-items: center; justify-content: center;
    gap: 40px;
  }
  .card {
    position: relative;
    width: 630px; height: 360px;
    background: var(--card);
    border-radius: 18px;
    box-shadow: 0 10px 28px rgba(0,0,0,.45);
    overflow: hidden;
  }
  .brand-name {
    display: flex; align-items: center; gap: 12px;
    font-weight: 800; text-transform: uppercase; letter-spacing: .06em;
    color: var(--text-light); line-height: 1.1;
  }
  .brand-mark { width: 16px; height: 16px; background: var(--accent); flex: none; }

  /* Front */
  .card-front { display: flex; align-items: center; justify-content: center; }
  .card-front .brand-name { font-size: 28px; }

  /* Back */
  .card-back .brand-name {
    position: absolute; left: 40px; top: 56px; font-size: 19px; max-width: 260px;
  }
  .owner { position: absolute; right: 40px; top: 70px; text-align: right; }
  .owner-name {
    font-weight: 800; font-size: 30px; color: var(--accent);
    text-transform: uppercase; letter-spacing: .03em;
  }
  .owner-title { font-size: 15px; margin-top: 2px; }
  .divider {
    position: absolute; left: 40px; right: 40px; top: 178px;
    height: 1px; background: var(--rule);
  }
  .contacts {
    position: absolute; left: 40px; bottom: 40px;
    list-style: none; display: flex; flex-direction: column; gap: 10px;
    font-size: 17px; letter-spacing: .02em;
  }
  .contacts li { display: flex; align-items: center; gap: 12px; }
  .contacts svg { width: 16px; height: 16px; flex: none; }
  .contacts .highlight { color: var(--accent); }
  .address {
    position: absolute; right: 40px; top: 206px;
    text-align: right; font-size: 15px; line-height: 1.5; letter-spacing: .03em;
  }
</style>
</head>
<body>
<main class="sheet">
  <section class="card card-front" aria-label="Card front">
    <div class="brand-name"><span class="brand-mark"></span>Bramblewood Card Company</div>
  </section>

  <section class="card card-back" aria-label="Card back">
    <div class="brand-name"><span class="brand-mark"></span>Bramblewood Card Company</div>

    <div class="owner">
      <p class="owner-name">Dalen Ashcroft</p>
      <p class="owner-title">CEO/Founder</p>
    </div>

    <div class="divider"></div>

    <ul class="contacts">
      <li>
        <svg viewBox="0 0 16 16" aria-hidden="true"><path fill="var(--accent)" d="M3.5 1.5l2.5 3-1.5 1.5c.8 1.9 2.1 3.2 4 4l1.5-1.5 3 2.5-1.5 2.5C7 13.3 2.7 9 1 3z"/></svg>
        <span>(123) 456 7890</span>
      </li>
      <li>
        <svg viewBox="0 0 16 16" aria-hidden="true"><rect x="1" y="3" width="14" height="10" rx="1" fill="var(--accent)"/><path d="M1.5 3.8L8 9l6.5-5.2" fill="none" stroke="var(--card)" stroke-width="1.4"/></svg>
        <span>info@bramblewoodcardco.com</span>
      </li>
      <li>
        <svg viewBox="0 0 16 16" aria-hidden="true"><g fill="none" stroke="var(--accent)" stroke-width="1.3"><circle cx="8" cy="8" r="6.5"/><ellipse cx="8" cy="8" rx="2.8" ry="6.5"/><path d="M1.5 8h13M2.5 4.8h11M2.5 11.2h11"/></g></svg>
        <span>www.<span class="highlight">bramblewoodcardco</span>.com</span>
      </li>
    </ul>

    <address class="address" style="font-style:normal">
      P.O. Box 2145 Street<br>
      Country Name AB 8542
    </address>
  </section>
</main>
</body>
</html>
```